QuillVane needs a dashboard page designed

Redesign the dashboard shown in the provided images.

There are two images:
- dashboard.png
- dashboard-expanded.png

NOTE: The vocabulary navigation on the left will be a very long list of words 100s, so keep that in mind when you're designing both the vocab navigation and the expanded vocab popup.

In the dashboard.png picture, there needs to be a progress chart showing the word progress like the following: review 1(show it as completed) -> review 2(show the user they are here) -> review 3(unvisited) -> review 4(unvisited)

The do-not-design-this-page.png image is for your reference only. It is not to be designed. Use it to understand the overall look and feel of the website to help you create the best dashboard page possible.
Updates

Need extra days to review

Industry/Entity Type

Education English learning

Number of Pages Required

1 page

Requirements
Must have
• The main navigation and main header cannot change between pages. See the do-not-design page for the main navigateion and header.
Should not have
• Do not add a person profile. We will not have images of our users. Keep the icons in the main navigation as they are.

```html
<!DOCTYPE html>
<html lang="en">
<head>
<meta charset="utf-8">
<title>QuillVane Tutor – Grab</title>
<link href="https://fonts.googleapis.com/css2?family=Lato:wght@400;700&display=swap" rel="stylesheet">
<style>
  :root {
    --sidebar-bg: #2b3238;
    --sidebar-text: #ffffff;
    --sidebar-sub: #b9bec3;
    --accent: #2f62ae;
    --done: #b0282f;
    --track: #dcdcdc;
    --ink: #1a1a1a;
    --body: #6a6a6a;
    --muted: #9a9a9a;
    --line: #e6e6e6;
    --page: #ffffff;
    --star: #f5b800;
  }
  * { box-sizing: border-box; margin: 0; padding: 0; }
  html, body { width: 1200px; height: 792px; overflow: hidden; background: var(--page); font-family: 'Lato', sans-serif; }
  .app { position: relative; width: 1200px; height: 792px; }

  .sidebar { position: absolute; left: 0; top: 0; width: 256px; height: 792px; background: var(--sidebar-bg); color: var(--sidebar-text); }
  .avatar { position: absolute; left: 84px; top: 40px; width: 88px; height: 88px; }
  .user-name { position: absolute; top: 140px; width: 256px; text-align: center; font-size: 17px; }
  .user-email { position: absolute; top: 164px; width: 256px; text-align: center; font-size: 13px; }
  .nav-item { position: absolute; left: 0; height: 31px; width: 256px; display: flex; align-items: center; font-size: 15.5px; }
  .nav-item svg { position: absolute; left: 50px; width: 24px; height: 24px; }
  .nav-item span { position: absolute; left: 91px; }
  .nav-item.active { background: var(--accent); width: 227px; border-radius: 0 16px 16px 0; }
  .sub-list { position: absolute; left: 91px; top: 379px; list-style: none; }
  .sub-list li { height: 21.4px; font-size: 13px; color: var(--sidebar-sub); line-height: 21.4px; }

  .topbar { position: absolute; left: 256px; top: 0; width: 944px; height: 41px; border-bottom: 1px solid var(--line); }
  .product-switch { position: absolute; left: 24px; top: 13px; font-size: 16px; color: var(--ink); }
  .product-switch svg { margin-left: 12px; vertical-align: middle; }
  .word-title { position: absolute; left: 386px; top: 11px; font-size: 18px; font-weight: 700; color: var(--ink); display: flex; align-items: center; gap: 6px; }
  .menu-icon { position: absolute; left: 894px; top: 10px; }

  .review-card { position: absolute; top: 66px; width: 199px; height: 77px; background: #fff; box-shadow: 0 1px 6px rgba(0,0,0,.12); }
  .review-card h3 { position: absolute; left: 23px; top: 18px; font-size: 18px; font-weight: 400; color: var(--ink); word-spacing: 8px; }
  .review-card .bar { position: absolute; left: 23px; top: 116px; }
  .bar-track { position: absolute; left: 23px; top: 50px; width: 153px; height: 8px; border-radius: 4px; background: var(--track); overflow: hidden; }
  .bar-fill { height: 100%; border-radius: 4px; }
  .review-card.done .bar-fill { width: 100%; background: var(--done); }
  .review-card.current { border: 1.5px solid var(--accent); box-shadow: none; }
  .review-card.current .bar-track { background: #fff; border: 1px solid #bbb; }
  .review-card.current .bar-fill { width: 65%; background: var(--accent); border-radius: 4px 0 0 4px; }
  .review-card.locked h3 { color: var(--muted); }

  .word-story, .analysis-text { position: absolute; left: 283px; width: 870px; font-size: 15.4px; line-height: 27.4px; color: var(--body); }
  .word-story { top: 180px; }
  .section-title { position: absolute; left: 283px; font-size: 17.5px; font-weight: 400; color: var(--ink); }
  .graph-title { top: 323px; }
  .analysis-title { top: 607px; }
  .analysis-text { top: 643px; }
  .curve-graph { position: absolute; left: 283px; top: 380px; }
  .curve-graph text { font-family: 'Lato', sans-serif; }
  .axis-caption { position: absolute; left: 700px; top: 568px; font-size: 15px; color: var(--ink); }
</style>
</head>
<body>
<div class="app">
  <aside class="sidebar">
    <svg class="avatar" viewBox="0 0 88 88" aria-hidden="true">
      <circle cx="44" cy="44" r="42" fill="#fff"/>
      <circle cx="44" cy="44" r="36" fill="var(--sidebar-bg)"/>
      <circle cx="44" cy="44" r="32" fill="#fff"/>
      <circle cx="44" cy="34" r="12" fill="var(--sidebar-bg)"/>
      <path d="M22 66 q0-18 22-18 q22 0 22 18 z" fill="var(--sidebar-bg)"/>
    </svg>
    <div class="user-name">Rowan</div>
    <div class="user-email">hello@quillvane-mail.com</div>

    <div class="nav-item" style="top:203px">
      <svg viewBox="0 0 24 24"><path d="M2 12 L12 3 L22 12 H19 V21 H14 V15 H10 V21 H5 V12 Z" fill="#fff"/></svg>
      <span>QuillVane Tutor</span></div>
    <div class="nav-item" style="top:234px">
      <svg viewBox="0 0 24 24"><circle cx="12" cy="11" r="10" fill="#fff"/><path d="M7 19 L5 23 L11 20 Z" fill="#fff"/><text x="12" y="14" font-size="7" font-weight="700" text-anchor="middle" fill="var(--sidebar-bg)">ENG</text></svg>
      <span>Daily English</span></div>
    <div class="nav-item" style="top:270px">
      <svg viewBox="0 0 24 24"><path d="M4 21 V3 H12 V21 Z M13 21 V9 H20 V21 Z" fill="#fff"/><g fill="var(--sidebar-bg)"><rect x="6" y="6" width="2" height="2"/><rect x="9" y="6" width="2" height="2"/><rect x="6" y="10" width="2" height="2"/><rect x="9" y="10" width="2" height="2"/><rect x="6" y="14" width="2" height="2"/><rect x="15" y="12" width="2" height="2"/><rect x="15" y="16" width="2" height="2"/></g></svg>
      <span>Business</span></div>
    <div class="nav-item" style="top:302px">
      <svg viewBox="0 0 24 24"><circle cx="12" cy="12" r="10" fill="none" stroke="#fff" stroke-width="1.5" stroke-dasharray="3 2"/><circle cx="12" cy="12" r="7" fill="#fff"/><path d="M12 8 V12 L15 14" stroke="var(--sidebar-bg)" stroke-width="1.6" fill="none"/></svg>
      <span>Short-Term Memory</span></div>
    <div class="nav-item active" style="top:340px">
      <svg viewBox="0 0 24 24"><path d="M4 21 V15 Q2 13 3 9 Q5 3 11 3 Q17 4 17 10 L19 13 H17 V17 H13 V21 Z" fill="#fff"/><circle cx="11" cy="10" r="3" fill="var(--accent)"/><circle cx="19" cy="5" r="3" fill="none" stroke="#fff" stroke-width="1.3"/></svg>
      <span>Working Memory</span></div>
    <ul class="sub-list">
      <li>Cool Down</li><li>Crave</li><li>Go For</li><li>Go-To</li><li>In The Mood For</li>
      <li>Sip</li><li>Soothing</li><li>Stick With</li><li>Throw In/Throw On</li>
    </ul>
    <div class="nav-item" style="top:579px">
      <svg viewBox="0 0 24 24"><circle cx="12" cy="12" r="10" fill="none" stroke="#fff" stroke-width="1.5" stroke-dasharray="3 2"/><circle cx="12" cy="12" r="7" fill="#fff"/><circle cx="12" cy="12" r="3" fill="var(--sidebar-bg)"/></svg>
      <span>Long-Term Memory</span></div>
  </aside>

  <header class="topbar">
    <div class="product-switch">QuillVane Tutor<svg width="15" height="9" viewBox="0 0 15 9"><path d="M0 0 H15 L7.5 9 Z" fill="var(--ink)"/></svg></div>
    <div class="word-title">Grab
      <svg width="24" height="23" viewBox="0 0 24 23"><path d="M12 0 L15 8 L24 8.5 L17 14 L19.5 23 L12 18 L4.5 23 L7 14 L0 8.5 L9 8 Z" fill="var(--star)"/></svg></div>
    <svg class="menu-icon" width="25" height="20" viewBox="0 0 25 20"><path d="M0 1 H25 M0 10 H25 M0 19 H25" stroke="var(--ink)" stroke-width="2"/></svg>
  </header>

  <section class="review-card done" style="left:284px"><h3>Reviews 1</h3><div class="bar-track"><div class="bar-fill"></div></div></section>
  <section class="review-card current" style="left:506px"><h3>Reviews 2</h3><div class="bar-track"><div class="bar-fill"></div></div></section>
  <section class="review-card locked" style="left:729px"><h3>Reviews 3</h3><div class="bar-track"></div></section>
  <section class="review-card locked" style="left:952px"><h3>Reviews 4</h3><div class="bar-track"></div></section>

  <p class="word-story">The word "grab' is most commonly used as a verb, meaning to take something quickly or suddenly. Imagine you're running late for school. You don't have time for breakfast, so you quickly grab an apple from the kitchen and rush out the door. As you reach the bus stop, your friend waves and says, "Hey! Let's grab a coffee after class." Later, when you sit down, your phone starts ringing. You grab it from your bag and answer.</p>

  <h2 class="section-title graph-title">Learning Curve Graph</h2>
  <svg class="curve-graph" width="905" height="185" viewBox="0 0 905 185">
    <g font-size="8" fill="#111">
      <text x="12" y="23">Long-Term Memory</text>
      <text x="13" y="81">Working Memory</text>
      <text x="12" y="128">Short-Term Memory</text>
      <text x="12" y="147">Forgotten Memory</text>
    </g>
    <line x1="10" y1="158" x2="897" y2="158" stroke="#222" stroke-width="1"/>
    <g stroke="#222">
      <line x1="16" y1="158" x2="16" y2="162"/><line x1="104" y1="158" x2="104" y2="162"/><line x1="192" y1="158" x2="192" y2="162"/>
      <line x1="280" y1="158" x2="280" y2="162"/><line x1="368" y1="158" x2="368" y2="162"/><line x1="456" y1="158" x2="456" y2="162"/>
      <line x1="543" y1="158" x2="543" y2="162"/><line x1="631" y1="158" x2="631" y2="162"/><line x1="719" y1="158" x2="719" y2="162"/>
      <line x1="807" y1="158" x2="807" y2="162"/><line x1="895" y1="158" x2="895" y2="162"/>
    </g>
    <rect x="92" y="124" width="17" height="34" fill="var(--accent)"/>
    <rect x="179" y="40" width="17" height="118" fill="var(--accent)"/>
    <path d="M111 125 Q150 128 180 157" fill="none" stroke="#333" stroke-width="1.6" stroke-dasharray="1.5 3"/>
    <path d="M197 40 Q250 44 266 49 Q330 70 373 160" fill="none" stroke="#333" stroke-width="1.6" stroke-dasharray="1.5 3"/>
    <g font-size="8" fill="#111">
      <rect x="73" y="98" width="39" height="22" fill="#fff" style="filter:drop-shadow(0 1px 2px rgba(0,0,0,.25))"/>
      <text x="92.5" y="112" text-anchor="middle">May 18</text>
      <rect x="146" y="29" width="41" height="21" fill="#fff" style="filter:drop-shadow(0 1px 2px rgba(0,0,0,.25))"/>
      <text x="166.5" y="42" text-anchor="middle">May 19</text>
    </g>
    <g font-size="8" fill="#111" text-anchor="middle">
      <text x="26" y="175">18 May</text><text x="70" y="175">12:00</text>
      <text x="113" y="175">19 May</text><text x="157" y="175">12:00</text>
      <text x="201" y="175">20 May</text><text x="245" y="175">12:00</text>
      <text x="289" y="175">21 May</text><text x="333" y="175">12:00</text>
      <text x="377" y="175">22 May</text><text x="421" y="175">12:00</text>
      <text x="464" y="175">23 May</text><text x="508" y="175">12:00</text>
      <text x="552" y="175">24 May</text><text x="596" y="175">12:00</text>
      <text x="640" y="175">25 May</text><text x="684" y="175">12:00</text>
      <text x="728" y="175">26 May</text><text x="772" y="175">12:00</text>
      <text x="815" y="175">27 May</text><text x="859" y="175">12:00</text>
      <text x="893" y="175">28…</text>
    </g>
  </svg>
  <div class="axis-caption">Date Range</div>

  <h2 class="section-title analysis-title">QuillVane Tutor Learning Analysis</h2>
  <p class="analysis-text">Lorem ipsum dolor sit amet, consectetur adipiscing elit. Nam rutrum commodo enim id bibendum. Nunc dignissim risus erat, nec finibus nunc dictum eu. Aliquam sit amet euismod metus, quis malesuada erat. Sed at felis quis nulla feugiat cursus at at dolor. Maecenas pretium aliquet dapibus. Fusce et eleifend massa. Sed convallis ex mi, at lobortis ligula congue vel.</p>
</div>
</body>
</html>
```